Recto Verso Audiology Business Card

Business card with a beautiful design on the back. On the Recto you need the following data Lindqvist Oren Audiologist Hearing Solutions Hearing Protection Tinnitus Hyperacusis Tel: 0482/37 59 08 Email: On the back, you need something nice like the attached file. The logo "Corra Luna" can be in the center The colors of the Logo can not be changed If possible stay in the same colors as the logo Another solution is to put the logo on the front and have a nice back (A mosaic of small ears, hearing aids or other ..) Thank you _______________________________________________________________ Visit card On the Recto Lindqvist Oren Audiologist Hearing Solutions Hearing Protection Tinnitus Hyperacusis Tel: 0482/37 59 08 Email: You can put the logo " Corra Luna "on the Recto of the Verso The colors of the logo can not be changed. If you put the logo on the back, it must be well integrated. On the Verso I need something in the files. something stylish. It's a visit card for an audiologist. You can get ears of hearing aids if you need. Thanks

Target Market(s)

customers

Contact Information for Business Card

Carte de visite standard ou A6

Font styles to use
Serif
Sans Serif

Colors
33a6d7

Requirements
Must have
• the logo and a stylized background.
Nice to have
• It would be nice to have a back side related to audiology (ears, hearing aids etc.)

```html
<!DOCTYPE html>
<html lang="en">
<head>
<meta charset="utf-8">
<title>Audiology Business Card – Recto Verso</title>
<link href="https://fonts.googleapis.com/css2?family=Barlow+Semi+Condensed:wght@300;400&display=swap" rel="stylesheet">
<style>
  :root {
    --backdrop: #1d1d1e;
    --card: #141516;
    --brand-cyan: #33a6d7;
    --name-cyan: #3bb0cf;
    --role-teal: #2c5d6b;
    --contact-grey: #b7bcc0;
    --logo-light: #e4e4e4;
    --foil-black: #0f1011;
    --foil-dark: #1c1d1f;
    --foil-mid: #3b3c3f;
    --foil-silver: #6d6e72;
  }
  * { margin: 0; padding: 0; box-sizing: border-box; }
  html, body {
    width: 1200px; height: 601px; overflow: hidden;
    background: var(--backdrop);
    font-family: "Barlow Semi Condensed", "Arial Narrow", sans-serif;
  }
  .canvas { position: relative; width: 1200px; height: 601px; }

  .card { position: absolute; background: var(--card); }
  .card--recto { left: 121px; top: 158px; width: 451px; height: 279px; }
  .card--verso { left: 633px; top: 157px; width: 465px; height: 281px; overflow: hidden; }

  .brand-name {
    position: absolute;
    font-weight: 300;
    text-transform: uppercase;
    letter-spacing: 0.01em;
  }
  .brand-name span { display: block; }
  .card--recto .brand-name {
    left: 49px; top: 66px;
    font-size: 30px; line-height: 32px;
    color: var(--brand-cyan);
  }
  .card--recto .brand-name .brand-gap { height: 13px; }
  .card--verso .brand-name {
    left: 164px; top: 83px;
    font-size: 26px; line-height: 27px;
    color: var(--logo-light);
  }
  .card--verso .brand-name .brand-gap { height: 11px; }

  .holder { position: absolute; left: 237px; top: 57px; }
  .holder-name {
    font-size: 19px; font-weight: 400;
    color: var(--name-cyan);
    text-transform: uppercase;
    letter-spacing: 0.03em;
    line-height: 1.1;
  }
  .holder-role {
    font-size: 12.5px; font-weight: 300;
    color: var(--role-teal);
    text-transform: uppercase;
    letter-spacing: 0.07em;
    margin-top: 1px;
  }
  .contact, .services {
    list-style: none;
    font-size: 13px; font-weight: 400;
    color: var(--contact-grey);
    line-height: 15px;
    letter-spacing: 0.02em;
  }
  .contact { margin-top: 14px; }
  .services { margin-top: 10px; }
  .services li { position: relative; padding-left: 12px; }
  .services li::before {
    content: ""; position: absolute; left: 1px; top: 6px;
    width: 3px; height: 3px; border-radius: 50%;
    background: var(--brand-cyan);
  }

  .ear-pattern {
    position: absolute; inset: 0;
    background:
      radial-gradient(ellipse 55% 70% at 22% 45%, rgba(120,121,126,0.55) 0%, rgba(120,121,126,0) 70%),
      linear-gradient(100deg, var(--foil-mid) 0%, var(--foil-silver) 22%, var(--foil-mid) 45%, var(--foil-dark) 72%, var(--foil-black) 100%);
  }
  .logo-plate {
    position: absolute; left: 158px; top: 77px;
    width: 146px; height: 130px;
    background: var(--card);
  }
</style>
</head>
<body>
<main class="canvas">

  <section class="card card--recto" aria-label="Card front">
    <div class="brand-name">
      <span>Medical</span>
      <span>Center</span>
      <span class="brand-gap"></span>
      <span>Corra</span>
      <span>Luna</span>
    </div>

    <div class="holder">
      <p class="holder-name">Lindqvist Oren</p>
      <p class="holder-role">Audiologist Hearing</p>
      <ul class="contact">
        <li>0482/37 59 08</li>
        <li>info@medicalcentercorraluna.com</li>
        <li>www.medicalcentercorraluna.com</li>
      </ul>
      <ul class="services">
        <li>Solutions Hearing</li>
        <li>Protection</li>
        <li>Tinnitus</li>
        <li>Hyperacusis</li>
      </ul>
    </div>
  </section>

  <section class="card card--verso" aria-label="Card back">
    <div class="ear-pattern" role="img" aria-label="Stylized audiology background: glossy silver foil mosaic of small ears with sound waves covering the whole card"></div>
    <div class="logo-plate"></div>
    <div class="brand-name">
      <span>Medical</span>
      <span>Center</span>
      <span class="brand-gap"></span>
      <span>Corra</span>
      <span>Luna</span>
    </div>
  </section>

</main>
</body>
</html>
```